"The Orginal LoopPeg's" needs a Package Design!! Everybody's got a LoopPeg, What's Yours?

I need eye popping packaging design!! My LoopPeg's are gonna be big! I'm a single mom I'm based in AZ, so this is big for me. The LoopPeg's keep towels off the floor & so much more!! Color cardboard insert background, bright yellow and Bright blue, like a caribbean blue, funky font for the Product Name. The Original, can be smaller and in an easy script. I have some pictures so you can get an concept and basic design ideas. There are no limits to their uses!! Please call me for any questions or direction.
Updates

I want to thank you all for participating, You each brought a different perspective and had some really good ideas. I will definitely us this service again! Thank you, Dolores Fitzwick

Target Market(s)

Mom's, woman, men, students you name it!!

Colors
fbee3e
0293ce

Requirements
Must have
• Clear pvc packaging so you can see the product and they have to hang over so you see how they are used. The look needs to draw people in to it!! Read my instructions on the downloaded pics and info and if you have questions please let me know. The towel and towel bar can be like a drawing not actual towel picture. On the reverse side is a list of ideas and my website. Other colors for lettering aside from the Caribbean blue for the word "LoopPeg's" is up to you, use your expertise.
Should not have
• The blue is not on the color wheel that is shown here.

```html
<!DOCTYPE html>
<html lang="en">
<head>
<meta charset="utf-8">
<title>The Orginal LoopPeg's – Package Insert</title>
<link rel="stylesheet" href="https://fonts.googleapis.com/css2?family=Fredoka:wght@600&family=Bangers&family=Nunito:wght@800;900&family=Varela+Round&display=swap">
<style>
  :root{
    --yellow:#fbee3e;
    --yellow-soft:#fdf6a0;
    --blue:#0293ce;
    --blue-light:#5ab8e0;
    --red:#e8202a;
    --white:#ffffff;
    --backdrop:#8a5a32;
  }
  *{margin:0;padding:0;box-sizing:border-box}
  html,body{width:1200px;height:796px;overflow:hidden}
  body{background:var(--backdrop);position:relative;font-family:"Nunito",Arial,sans-serif}

  /* ---------- front card ---------- */
  .front{position:absolute;left:28px;top:108px;width:552px;height:663px;background:var(--yellow)}
  .brand{position:absolute;left:0;right:0;top:38px;text-align:center;color:var(--blue);
    font-family:"Fredoka",sans-serif;font-weight:600;line-height:1}
  .brand .lead{display:block;font-size:24px;margin-bottom:4px}
  .brand .name{display:block;font-size:64px}
  .tagline-band{position:absolute;left:0;right:0;top:160px;height:72px;background:var(--blue);
    border-top:4px solid var(--white);color:var(--white);text-align:center;
    font-family:Arial,Helvetica,sans-serif;font-weight:700;font-size:18px;line-height:28px;padding-top:8px}
  .window{position:absolute;left:75px;top:254px;width:414px;height:196px;background:var(--blue-light);
    border-radius:12px;padding:13px 12px 12px 15px}
  .window .product{width:100%;height:100%;border-radius:2px;
    background:linear-gradient(90deg,#a5245a 0 24%,#f0246e 24% 49%,#1f7ea0 49% 74%,#8ad63c 74% 100%)}
  .slogan{position:absolute;left:40px;top:475px;width:472px;height:105px;background:var(--blue);
    border:4px solid var(--white);color:var(--white);text-align:center;
    font-family:"Bangers",sans-serif;font-size:36px;letter-spacing:1.5px;line-height:38px;padding-top:12px}
  .count-badge{position:absolute;left:450px;top:528px;width:86px;height:86px;border-radius:50%;
    background:var(--blue);border:4px solid var(--white);color:var(--white);text-align:center;
    font-family:Arial,Helvetica,sans-serif;font-weight:700;font-size:10.5px;line-height:16px;padding-top:24px}
  .count-badge span{font-size:10px;font-weight:400}
  .note{position:absolute;left:0;width:552px;top:596px;padding-right:106px;text-align:center;
    color:var(--red);font-family:Arial,Helvetica,sans-serif;font-weight:700;font-size:13px}

  /* ---------- back card ---------- */
  .back{position:absolute;left:624px;top:32px;width:550px;height:661px;
    background:radial-gradient(ellipse at 50% 55%,var(--yellow-soft) 0%,var(--yellow) 60%)}
  .promo{position:absolute;left:0;right:0;top:58px;text-align:center;color:var(--blue);
    font-weight:900;font-size:15px;line-height:22px;text-transform:uppercase;letter-spacing:.3px}
  .promo .hot{color:var(--red);font-size:20px}
  .promo .free{color:var(--red);font-size:19px}
  .promo .red{color:var(--red)}
  .uses-gallery{position:absolute;left:36px;top:135px;display:flex;gap:12px}
  .uses-gallery .shot{width:111px;height:128px;background:var(--blue);border-radius:10px;padding:7px;
    box-shadow:2px 3px 4px rgba(0,0,0,.25)}
  .uses-gallery .shot div{width:100%;height:100%;border-radius:4px}
  .shot .bib{background:linear-gradient(#c9b7a6,#6fb9e0)}
  .shot .dishtowel{background:linear-gradient(#f6f6f6 0 20%,#b8283a 20% 80%,#f6f6f6 80%)}
  .shot .wrap{background:linear-gradient(#f1f1ef 0 25%,#c8e29a 25%)}
  .shot .shade{background:linear-gradient(#7a6450 0 35%,#a9cde6 35%)}
  .uses{position:absolute;top:278px;list-style:none;color:var(--blue);
    font-family:"Varela Round",sans-serif;font-size:15.5px;line-height:21.6px}
  .uses.col-a{left:59px}
  .uses.col-b{left:282px}
  .uses li{position:relative;padding-left:18px}
  .uses li::before{content:"";position:absolute;left:0;top:4px;width:13px;height:13px;background:var(--blue);border-radius:2px}
  .uses li::after{content:"";position:absolute;left:4px;top:6px;width:4px;height:7px;
    border:solid var(--white);border-width:0 2px 2px 0;transform:rotate(40deg)}
  .closing{position:absolute;left:0;right:0;top:552px;text-align:center;color:var(--red);
    font-weight:900;font-size:20px;letter-spacing:1px}
  .site{position:absolute;left:0;right:0;top:585px;text-align:center;color:var(--red);
    font-family:Arial,Helvetica,sans-serif;font-weight:700;font-size:12.5px}
</style>
</head>
<body>

<section class="front">
  <h1 class="brand"><span class="lead">The Orginal</span><span class="name">LoopPeg's</span></h1>
  <div class="tagline-band">NO MORE TOWELS ON THE FLOOR<br>&amp; SO MUCH MORE!!!</div>
  <div class="window"><div class="product" role="img" aria-label="Four fabric loop pegs in patterned ribbon: dotted magenta, pink, dotted teal and lime green"></div></div>
  <div class="slogan">EVERYBODY'S GOT A LOOPPEG<br>WHAT'S YOURS?</div>
  <div class="count-badge">4 LOOPPEGS<br><span>per box</span></div>
  <p class="note">Thin clear rubber band to hold product in place.</p>
</section>

<section class="back">
  <p class="promo">
    <span class="hot">Endless uses</span> – post a picture of your<br>
    LoopPeg idea to our website and you could win<br>
    a <span class="free">free</span> package of <span class="red">limited edition LoopPegs'</span>!!
  </p>
  <div class="uses-gallery">
    <div class="shot"><div class="bib" role="img" aria-label="Photo of a toddler wearing a blue bib held by a loop peg"></div></div>
    <div class="shot"><div class="dishtowel" role="img" aria-label="Photo of a red dish towel hanging from a copper rail"></div></div>
    <div class="shot"><div class="wrap" role="img" aria-label="Photo of a green towel wrap fastened with a loop peg"></div></div>
    <div class="shot"><div class="shade" role="img" aria-label="Photo of a window shade pull-down made from a loop peg"></div></div>
  </div>
  <ul class="uses col-a">
    <li>Baby Bibs</li><li>Baby Strollers</li><li>Hanging Bathing Suits</li><li>By the Pool</li>
    <li>Pull downs for Shades</li><li>Tarp Holders</li><li>Camping</li><li>Room Dividers</li>
    <li>College Dorms</li><li>The Gym</li><li>Photography Backdrops</li><li>Traveling</li>
  </ul>
  <ul class="uses col-b">
    <li>Towel wraps</li><li>Pet Training</li><li>Drying Lingerie</li><li>Tablecloths</li>
    <li>Dishtowels</li><li>The Garage</li><li>Hanging Quilts</li><li>To hold your pants closed</li>
    <li>Curtains (no sewing!)</li><li>Valences (no sewing!)</li><li>Drapes (no sewing!)</li><li>Shower Curtains</li>
  </ul>
  <p class="closing">THE ONLY LIMIT IS YOUR IMAGINATION</p>
  <p class="site">The original LoopPegs.com</p>
</section>

</body>
</html>
```